Custom Cabinet Shop Needs a website design

Hi,
We need a website for a Custom Cabinet Shop and Cabinet parts manufacturing business.
The business has two sides to it. One side provides custom Kitchens, vanities, entertainment units, offices and what not to homeowners and contractors.
The 2nd side of the business provides built to order cabinet boxes and other parts required to put together a project to other cabinet shops, small contractors looking to install there own cabinets.
Website will need a Gallery to display work.
Color scheme to go well with logo.
current website is www.brambleoakcustomcabinets.com
being changed to www.brambleoak.ca
Logo Included in attached files.
Tagline "Joinery with Spirit"
Mission Statement "Our passion is to deliver inspired cabinetry solutions to suit all your needs, supported by our phenomenal star class customer service"
The website should convey quality and professionalism.
Thank you.
Homeowners/ Contractors
Entertainment

```html
<!DOCTYPE html>
<html lang="en">
<head>
<meta charset="utf-8">
<title>Brambleoak Custom Cabinets</title>
<link rel="stylesheet" href="https://fonts.googleapis.com/css2?family=Raleway:wght@400;500;600;700;800&family=Noto+Serif:ital@1&display=swap">
<style>
:root{
  --orange:#e8561e;
  --dark:#141414;
  --darker:#0c0c0c;
  --text:#555;
  --light:#fff;
  --rule:#c8c8c8;
  --foot-text:#a8a8a8;
}
*{margin:0;padding:0;box-sizing:border-box}
html,body{width:1046px;height:1200px;overflow:hidden;background:#fff}
body{position:relative;font-family:"Raleway",Arial,sans-serif;color:var(--text)}
.abs{position:absolute}
a{color:inherit;text-decoration:none}

/* header */
.brand{left:94px;top:34px;display:flex;align-items:center;gap:10px}
.brand-mark{width:34px;height:34px;border-radius:50%;background:var(--orange)}
.brand-name{font-weight:800;font-size:25px;color:var(--dark);letter-spacing:.5px}
.call{left:758px;top:34px;display:flex;gap:12px;align-items:center}
.call-label{font-size:14px;color:var(--dark);font-weight:500}
.call-number{font-size:21px;color:var(--orange);font-weight:700;line-height:1.1}

/* nav */
.nav{left:0;top:110px;width:1046px;height:50px;background:var(--dark)}
.nav-item{top:0;height:50px;line-height:50px;color:#fff;font-size:12.5px;font-weight:500}
.nav-sep{top:0;width:2px;height:50px;background:#2b2b2b;border-right:1px solid #000}
.social{top:118px;width:31px;height:31px;border-radius:50%;background:var(--orange)}

/* hero */
.hero{left:0;top:160px;width:1046px;height:404px;background:linear-gradient(180deg,#c9b9a3 0%,#e2dad0 45%,#b7aa9a 80%,#4a3628 100%)}
.hero-tag{left:343px;top:308px;width:360px;height:50px;background:var(--orange);opacity:.93;color:#fff;font-family:"Noto Serif",Georgia,serif;font-style:italic;font-size:31px;text-align:center;line-height:50px}
.hero-title{left:271px;top:364px;width:505px;height:51px;background:rgba(30,30,30,.88);color:#fff;font-family:"Noto Serif",Georgia,serif;font-style:italic;font-size:30px;font-weight:400;text-align:center;line-height:51px}

/* sections */
.sec-head{top:593px;font-size:17.5px;font-weight:600;color:#333}
.sec-head span{color:var(--orange)}
.sec-rule{top:624px;height:1px;background:var(--rule)}
.sec-rule::before{content:"";position:absolute;left:0;top:-1px;width:46px;height:3px;background:var(--dark)}
.photo-frame{left:103px;top:643px;width:256px;height:133px;background:#fff;box-shadow:0 0 3px rgba(0,0,0,.3);padding:5px}
.photo{width:100%;height:100%;background:linear-gradient(135deg,#5a3a2a,#d8cfc2 55%,#8a8680)}
.body-text{font-size:12.5px;line-height:19px;color:var(--text)}
.btn{left:106px;top:853px;width:91px;height:26px;background:var(--orange);color:#fff;font-size:13.5px;line-height:26px;text-align:center}
.btn::before{content:"";position:absolute;left:14px;top:-5px;border:5px solid transparent;border-top:0;border-bottom-color:var(--orange)}

.services{left:388px;top:645px;width:272px}
.service{margin-bottom:14px}
.svc-title{font-size:17px;font-weight:600;color:var(--orange);display:flex;align-items:center;gap:10px;line-height:22px}
.svc-text{font-size:12px;line-height:18.5px;color:var(--text);margin:7px 0 2px 2px;letter-spacing:-.1px}
.read-more{display:inline-block;font-size:12.5px;line-height:18px;color:var(--orange);text-decoration:underline;margin-left:1px}

.gallery-card{left:668px;top:646px;width:277px;height:228px;box-shadow:0 0 3px rgba(0,0,0,.25);background:#fff}
.gallery-photo{width:277px;height:106px;background:linear-gradient(135deg,#3c3f44,#c9c5bd 50%,#2e2a26)}
.gallery-title{left:12px;top:118px;font-size:14.5px;color:var(--orange);font-weight:500}
.gallery-text{left:12px;top:142px;width:255px;font-size:12.5px;line-height:19px}
.pager{left:0;top:197px;width:277px;height:31px;display:flex}
.pager div{height:31px;line-height:31px;text-align:center;color:#fff;font-weight:600;font-size:15px}
.pager .arrow{width:40px;background:var(--dark)}
.pager .num{width:39px;background:var(--orange);border-right:1px solid #fff}
.pager .num.active{position:relative}
.pager .num.active::before{content:"";position:absolute;left:14px;top:-6px;border:6px solid transparent;border-top:0;border-bottom-color:var(--orange)}

/* footer */
.footer{left:0;top:915px;width:1046px;height:234px;background:var(--dark)}
.foot-head{top:941px;font-size:15px;color:#fff;font-weight:500}
.foot-rule{top:973px;height:1px;background:#3a3a3a}
.foot-rule::before{content:"";position:absolute;left:0;top:-1px;width:46px;height:3px;background:var(--orange)}
.foot-list{top:995px;list-style:none;font-size:12.5px;color:var(--foot-text)}
.foot-list li{height:22.7px;line-height:22.7px}
.foot-list li::before{content:"›";margin-right:8px;color:#888}
.contact-row{display:flex;gap:10px;font-size:12.5px;color:var(--foot-text);line-height:19px}
.foot-phone{font-size:15.5px;color:#ddd;font-weight:500}
.foot-brand{left:750px;top:1022px;display:flex;align-items:center;gap:10px}
.foot-brand .brand-name{color:#fff;font-size:21px}
.bottom{left:0;top:1149px;width:1046px;height:51px;background:var(--darker);font-size:12px;color:#ccc;line-height:51px}
</style>
</head>
<body>

<header>
  <div class="abs brand" aria-label="Brambleoak Custom Cabinets">
    <span class="brand-mark"></span>
    <span class="brand-name">BRAMBLEOAK</span>
  </div>
  <div class="abs call">
    <svg width="36" height="40" viewBox="0 0 36 40" aria-hidden="true">
      <path d="M6 4c3-2 6 0 7 3l2 5c1 2-1 4-3 5 1 5 4 9 8 12 2-1 4-2 5 0l4 4c2 2 1 5-2 6-11 3-25-15-21-35z" fill="#111"/>
      <path d="M20 5a12 12 0 0 1 11 12" stroke="#e8561e" stroke-width="2.5" fill="none"/>
      <path d="M20 11a6 6 0 0 1 5 6" stroke="#e8561e" stroke-width="2.5" fill="none"/>
    </svg>
    <div>
      <div class="call-label">CALL US TODAY</div>
      <div class="call-number">403-555-0142</div>
    </div>
  </div>
</header>

<nav class="abs nav">
  <a class="abs nav-item" style="left:105px">HOME</a>
  <span class="abs nav-sep" style="left:169px"></span>
  <a class="abs nav-item" style="left:196px">GALLERY</a>
  <span class="abs nav-sep" style="left:278px"></span>
  <a class="abs nav-item" style="left:305px">SERVICES</a>
  <span class="abs nav-sep" style="left:390px"></span>
  <a class="abs nav-item" style="left:421px">WARRANTY</a>
  <span class="abs nav-sep" style="left:513px"></span>
  <a class="abs nav-item" style="left:545px">CONTACT</a>
</nav>
<span class="abs social" style="left:811px"></span>
<span class="abs social" style="left:848px"></span>
<span class="abs social" style="left:883px"></span>
<span class="abs social" style="left:918px"></span>

<section class="abs hero" role="img" aria-label="Photo of a bright white custom kitchen with stainless range and sunflowers by the window"></section>
<div class="abs hero-tag">Joinery with Spirit</div>
<h1 class="abs hero-title">Custom Cabinet Design Company</h1>

<!-- who we are -->
<h2 class="abs sec-head" style="left:103px"><span>WHO</span> WE ARE</h2>
<div class="abs sec-rule" style="left:103px;width:258px"></div>
<div class="abs photo-frame"><div class="photo" role="img" aria-label="Photo of a finished kitchen with island and pendant light"></div></div>
<p class="abs body-text" style="left:106px;top:785px;width:255px">Lorem Ipsum is simply dummy text of the printing and typesetting industry. Lorem Ipsum has been the industry's and.</p>
<a class="abs btn">Read More</a>

<!-- what we do -->
<h2 class="abs sec-head" style="left:390px"><span>WHAT</span> WE DO</h2>
<div class="abs sec-rule" style="left:390px;width:245px"></div>
<div class="abs services">
  <div class="service">
    <div class="svc-title"><svg width="20" height="18" viewBox="0 0 20 18" aria-hidden="true"><path d="M11 1l2 6h6l-5 4 2 6-5-4-5 4 2-6-6-4h7z" fill="none" stroke="#111" stroke-width="1.4"/></svg>Residential</div>
    <p class="svc-text">Here at Brambleoak Custom Cabinets we are proud to be involved in the custom cabinet market. By employing and partnering....</p>
    <a class="read-more">Read More</a>
  </div>
  <div class="service">
    <div class="svc-title"><svg width="20" height="18" viewBox="0 0 20 18" aria-hidden="true"><path d="M11 1l2 6h6l-5 4 2 6-5-4-5 4 2-6-6-4h7z" fill="none" stroke="#111" stroke-width="1.4"/></svg>Business</div>
    <p class="svc-text">At Brambleoak Custom Cabinets we understand that contractors, renovators, home builders, design firms and designers are the...</p>
    <a class="read-more">Read More</a>
  </div>
</div>

<!-- gallery -->
<h2 class="abs sec-head" style="left:668px"><span>OUR</span> GALLERY</h2>
<div class="abs sec-rule" style="left:668px;width:277px"></div>
<div class="abs gallery-card">
  <div class="gallery-photo" role="img" aria-label="Photo of a white kitchen with dining table and stainless appliances"></div>
  <div class="abs gallery-title">Lorem Ipsum Dolor Sit amet Type</div>
  <p class="abs gallery-text">Lorem Ipsum is simply dummy text of the printing and typesetting industry.</p>
  <div class="abs pager">
    <div class="arrow">&lsaquo;</div>
    <div class="num active">1</div><div class="num">2</div><div class="num">3</div><div class="num">4</div><div class="num" style="border:0">5</div>
    <div class="arrow" style="margin-left:1px">&rsaquo;</div>
  </div>
</div>

<!-- footer -->
<footer class="abs footer"></footer>
<h3 class="abs foot-head" style="left:101px">Who We Are</h3>
<div class="abs foot-rule" style="left:103px;width:153px"></div>
<ul class="abs foot-list" style="left:104px">
  <li>Home</li><li>Gallery</li><li>Services</li><li>Warranty</li><li>Contact</li>
</ul>
<h3 class="abs foot-head" style="left:285px">Our Services</h3>
<div class="abs foot-rule" style="left:286px;width:189px"></div>
<ul class="abs foot-list" style="left:288px">
  <li>Lorem Ipsum Dolor Sit Amet</li><li>Typesetting Industry</li><li>Have been Sent in Lorem</li><li>Services Which Done</li><li>Inside Vehicula Quis</li>
</ul>
<h3 class="abs foot-head" style="left:511px">Contact Us</h3>
<div class="abs foot-rule" style="left:512px;width:189px"></div>
<div class="abs contact-row" style="left:513px;top:995px">
  <svg width="14" height="18" viewBox="0 0 14 18" aria-hidden="true"><path d="M7 0a7 7 0 0 1 7 7c0 5-7 11-7 11S0 12 0 7a7 7 0 0 1 7-7z" fill="#888"/><circle cx="7" cy="7" r="2.5" fill="#141414"/></svg>
  <div>4812 Range Road 290<br>Cedar Hollow, Alberta<br>T1X 5K2</div>
</div>
<div class="abs contact-row" style="left:512px;top:1053px;align-items:center">
  <svg width="16" height="18" viewBox="0 0 16 18" aria-hidden="true"><path d="M3 1c2-1 3 0 4 2l1 3c0 1-1 2-2 3 1 3 2 4 4 6 1-1 2-1 3 0l2 2c1 1 0 3-1 3C8 20-1 8 3 1z" fill="#888"/></svg>
  <span class="foot-phone">403-555-0187</span>
</div>
<div class="abs contact-row" style="left:513px;top:1086px;align-items:center">
  <svg width="17" height="12" viewBox="0 0 17 12" aria-hidden="true"><rect width="17" height="12" fill="#888"/><path d="M0 0l8.5 7L17 0" stroke="#141414" fill="none"/></svg>
  <span>sales@brambleoakcabinets.com</span>
</div>
<div class="abs foot-brand" aria-label="Brambleoak Custom Cabinets">
  <span class="brand-mark" style="width:28px;height:28px"></span>
  <span class="brand-name">BRAMBLEOAK</span>
</div>

<div class="abs bottom">
  <span class="abs" style="left:100px">copyright©2015.Bramble Oak Cabinet. All Rights Reserved</span>
  <span class="abs" style="left:744px">Privacy Policy&nbsp;&nbsp;&nbsp;&nbsp;|&nbsp;&nbsp;&nbsp;&nbsp;Terms &amp; Conditions</span>
</div>

</body>
</html>
```